Tavel Website

Need a 4 page Drupal website - Home, About Us, Portfolio, Contact for a private equity/venture capital firm and new logo - company name is Tavel Corporation. The design should communicate - stock markets, hedge funds, deal-making, investments. The Portfolio section is to showcase the small companies we invest in. Hoping for something fresh, dynamic, even fun - no cliche financial images of New York. Not technical - but know how use Drupal content management to make text edits, blocks, articles, etc. We don't use any social media - so no chirply, Pagebook or WorkNode links. We need space for a post heron email sign-up form. Need website uploaded to my Corvane web hosting account. First time user of Sketch Plaza - have 3 other company websites that need refreshing.

```html
<!DOCTYPE html>
<html lang="en">
<head>
<meta charset="utf-8">
<title>Tavel Corporation</title>
<link href="https://fonts.googleapis.com/css2?family=Mulish:wght@400;600;700&family=Open+Sans:wght@400;600;700&display=swap" rel="stylesheet">
<style>
:root{
  --blue-top:#2f8ab8;
  --blue-bottom:#135a88;
  --nav-bg:#0f4e7a;
  --sky:#8fd6f4;
  --title-blue:#1d5e8c;
  --link-blue:#1f6f9f;
  --ink:#1d1d1d;
  --body:#6b6b6b;
  --orange:#f7a400;
  --orange-dark:#f39200;
  --line:#e3e3e3;
  --footer-bg:#f6f6f6;
  --footer-ink:#4a4a4a;
  --partner:#3b4a5a;
}
*{margin:0;padding:0;box-sizing:border-box}
html,body{width:1200px;height:1159px;overflow:hidden;background:#fff}
body{font-family:"Open Sans",sans-serif;color:var(--body)}
.canvas{position:relative;width:1200px;height:1159px;overflow:hidden}

/* header */
.site-header{position:absolute;left:0;top:0;width:1200px;height:107px;
  background:linear-gradient(180deg,var(--blue-top),var(--blue-bottom));
  border-bottom:1px solid #0b3f63}
.brand{position:absolute;left:112px;top:33px;font-family:"Mulish",sans-serif;color:#fff;font-size:31px;font-weight:400;line-height:1;white-space:nowrap}
.slogan{position:absolute;left:253px;top:70px;font-family:"Mulish",sans-serif;font-size:13px;color:var(--sky);white-space:nowrap}
.phone{position:absolute;left:933px;top:16px;display:flex;align-items:center;gap:6px;color:#fff;font-family:"Mulish",sans-serif;font-size:20px;font-weight:600;white-space:nowrap}
.main-nav{position:absolute;left:605px;top:58px;width:480px;height:49px}
.main-nav svg{position:absolute;left:0;top:0}
.main-nav ul{position:absolute;left:0;top:0;width:100%;height:100%;list-style:none;display:flex;align-items:center;padding-left:41px;font-family:"Mulish",sans-serif;font-size:15px;font-weight:600;white-space:nowrap}
.main-nav li{color:#cfe6f5;display:flex;align-items:center}
.main-nav li.active{color:#fff}
.main-nav li+li::before{content:"|";color:#7fb2d3;margin:0 20px;font-weight:400}

/* hero */
.hero{position:absolute;left:0;top:107px;width:1200px;height:505px;
  background:linear-gradient(90deg,#9ec2e0 0%,#d9e2e6 28%,#8b9197 50%,#d5dadd 70%,#e9a493 100%)}
.hero-caption{position:absolute;left:296px;top:168px;width:621px;height:134px;background:rgba(255,255,255,.88);text-align:center;font-family:"Mulish",sans-serif}
.hero-caption h1{margin-top:26px;font-size:37px;font-weight:600;color:var(--title-blue);white-space:nowrap}
.hero-caption p{margin-top:4px;font-size:19px;color:var(--link-blue);white-space:nowrap}
.slider-dots{position:absolute;left:579px;top:478px;display:flex;gap:3px}
.slider-dots span{width:13px;height:13px;border-radius:50%;background:#fff}

/* intro */
.welcome{position:absolute;left:113px;top:656px;width:480px}
.welcome h2{font-family:"Mulish",sans-serif;font-weight:400;font-size:27px;color:var(--ink);margin-bottom:11px;white-space:nowrap}
.welcome p{font-size:12.3px;line-height:21px;margin-bottom:11px;padding-left:1px;letter-spacing:-.1px}
.btn-primary{display:inline-block;margin-top:4px;margin-left:1px;width:116px;height:34px;line-height:34px;text-align:center;color:#fff;font-family:"Mulish",sans-serif;font-size:14px;background:linear-gradient(180deg,var(--orange),var(--orange-dark))}

.feature{position:absolute;top:663px;width:218px}
.feature-1{left:626px}
.feature-2{left:871px}
.feature .thumb{width:215px;height:96px}
.feature-1 .thumb{background:linear-gradient(135deg,#e8e4df,#b89f8c 55%,#3f4a5a)}
.feature-2 .thumb{background:linear-gradient(135deg,#8a8f96,#2c3540 45%,#3c9a4c 80%,#d9a48a)}
.feature h3{font-family:"Mulish",sans-serif;font-weight:400;font-size:18.5px;color:var(--link-blue);margin:8px 0 6px;white-space:nowrap;letter-spacing:-.1px}
.feature p{font-size:11.4px;line-height:19px}
.more{display:flex;align-items:center;gap:4px;margin-top:4px;font-family:"Mulish",sans-serif;font-size:12.5px;font-weight:700;color:var(--title-blue)}

/* partners */
.partners{position:absolute;left:0;top:937px;width:1200px;height:85px;border-top:1px solid var(--line);display:flex;align-items:center;padding-left:114px;white-space:nowrap}
.partners h2{font-family:"Mulish",sans-serif;font-weight:400;font-size:22px;color:var(--orange);margin-right:36px}
.partner{display:flex;align-items:center;gap:5px;font-family:"Mulish",sans-serif;font-weight:700;font-size:15px;color:var(--partner);margin-right:27px}
.partner i{display:block;width:10px;height:10px;background:var(--partner)}
.partner i.round{border-radius:50%}

/* footer */
.site-footer{position:absolute;left:0;top:1022px;width:1200px;height:137px;background:var(--footer-bg)}
.footer-nav{position:absolute;left:110px;top:38px;font-family:"Mulish",sans-serif;font-size:14px;color:var(--footer-ink);display:flex;white-space:nowrap}
.footer-nav span+span::before{content:"|";margin:0 6px}
.copyright{position:absolute;left:111px;top:67px;font-size:12px;color:#888;white-space:nowrap}
.newsletter{position:absolute;left:843px;top:38px}
.newsletter h3{font-family:"Mulish",sans-serif;font-weight:400;font-size:14px;color:var(--footer-ink);white-space:nowrap}
.subscribe{display:flex;margin-top:9px;width:226px;height:29px}
.subscribe .field{flex:1;background:#fff;border:1px solid #ddd;font-size:12px;color:#888;line-height:27px;padding-left:10px}
.subscribe .go{width:27px;background:var(--orange);display:flex;align-items:center;justify-content:center}
</style>
</head>
<body>
<div class="canvas">

  <header class="site-header">
    <div class="brand">Tavel Corporation</div>
    <div class="slogan">Slogan goes here</div>
    <div class="phone">
      <svg width="22" height="22" viewBox="0 0 22 22" aria-hidden="true"><circle cx="11" cy="11" r="10" fill="none" stroke="#a9cfe6" stroke-width="1.4"/><path d="M8 6.5c-.8.4-1.4 1.2-1.2 2.3.5 3 3.4 6 6.4 6.5 1 .2 1.9-.4 2.3-1.2l-1.9-1.4-1.1.8c-1.4-.6-2.6-1.8-3.2-3.2l.8-1.1z" fill="#a9cfe6"/></svg>
      555-010-2733
    </div>
    <nav class="main-nav">
      <svg width="480" height="49" aria-hidden="true"><path d="M18 0H480V49H0Z" fill="var(--nav-bg)"/></svg>
      <ul>
        <li class="active">HOME</li>
        <li>ABOUT US</li>
        <li>PORTFOLIO</li>
        <li>CONTACT</li>
      </ul>
    </nav>
  </header>

  <section class="hero" role="img" aria-label="Photo of a smiling advisor in a grey suit meeting with a couple across a desk">
    <div class="hero-caption">
      <h1>Investment &amp; Stock Market Tips</h1>
      <p>Vivamus porttitor purus nisi eleifend libero tempus libero</p>
    </div>
    <div class="slider-dots"><span></span><span></span><span></span><span></span></div>
  </section>

  <section class="welcome">
    <h2>Welcome to Tavel Corporation</h2>
    <p>Etiam est nunc venenatis in tristique eu imperdiet ac nisl Cum sociis natoque penatibus et magnis dis parturient montes nascetur ridiculus mus In iaculis facilisis massa Etiam eu urna Sed porta Suspendisse quam leo molestie sed luct</p>
    <p>Sed metus augue convallis et vehicula ut pulvinar eu ante Integer orci tellus tristique vitae consequat nec porta vel lectus Nulla sit amet diam Duis non nunc</p>
    <span class="btn-primary">READ MORE</span>
  </section>

  <article class="feature feature-1">
    <div class="thumb" role="img" aria-label="Photo of a couple saving money with a piggy bank"></div>
    <h3>Investment &amp; Marketing</h3>
    <p>Vivamus porttitor g purus nisi eleifend libero a tempus libero lectus feugiat felis Morbi diam mauris viverra</p>
    <span class="more">READ MORE <svg width="6" height="9" viewBox="0 0 6 9" aria-hidden="true"><path d="M0 0L6 4.5 0 9Z" fill="#2a9fd6"/></svg></span>
  </article>

  <article class="feature feature-2">
    <div class="thumb" role="img" aria-label="Photo of hands holding a tablet showing a stock market chart"></div>
    <h3>Stock Markets</h3>
    <p>Vivamus porttitor g purus nisi eleifend libero a tempus libero lectus feugiat felis Morbi diam mauris viverra</p>
    <span class="more">READ MORE <svg width="6" height="9" viewBox="0 0 6 9" aria-hidden="true"><path d="M0 0L6 4.5 0 9Z" fill="#2a9fd6"/></svg></span>
  </article>

  <section class="partners">
    <h2>Our Portfolio</h2>
    <span class="partner"><i class="round"></i>Orvella</span>
    <span class="partner">BRIGHTMERE</span>
    <span class="partner">Lumacore</span>
    <span class="partner"><i></i>Dexlight</span>
    <span class="partner">PRIMWELL</span>
    <span class="partner">Sparrow Bio</span>
    <span class="partner"><i></i>Harbor Trust</span>
  </section>

  <footer class="site-footer">
    <div class="footer-nav"><span>HOME</span><span>ABOUT US</span><span>PORTFOLIO</span><span>CONTACT</span></div>
    <div class="copyright">© 2014 Company Name &nbsp;All right reserved &nbsp;Term of Use</div>
    <div class="newsletter">
      <h3>NEWSLETTER SUBSCRIBE</h3>
      <div class="subscribe">
        <div class="field">email address</div>
        <div class="go"><svg width="6" height="9" viewBox="0 0 6 9" aria-hidden="true"><path d="M0 0L6 4.5 0 9Z" fill="#fff"/></svg></div>
      </div>
    </div>
  </footer>

</div>
</body>
</html>
```